Casino with the 'highest winning percentage' needs a stationery design

This is for a casino in Colombo, Sri Lanka and we need a stationery design for business card, letter head and envelope.

Should be very professional, simple and elegant without fancy fonts

Reason: Not fully satisfied with the designs. Need more designs.

Business

• 1. card deck symbol 'CLUBS' in red, or black

2. name in BLOCK CAPITAL LETTERS

3. Preferred font colours are black, white or red

4. Prefer 'professional /elegant' fonts
• SHOULD NOT HAVE ANY OTHER SYMBOL EXCEPT 'CLUBS'

DO NOT PREFER ITALIC FONTS

```html
<!DOCTYPE html>
<html lang="en">
<head>
<meta charset="utf-8">
<title>Corvane Casino – Business Card</title>
<link rel="stylesheet" href="https://fonts.googleapis.com/css2?family=Open+Sans:wght@400;700&display=swap">
<style>
  :root {
    --backdrop: #a9aab3;
    --card-white: #f4f4f4;
    --ink: #3a3a3c;
    --ink-soft: #6a6a6e;
    --card-dark: #2f3034;
    --pattern-light: #6c6d72;
    --pattern-dark: #26272a;
    --frame-line: #d9d9dc;
  }
  * { margin: 0; padding: 0; box-sizing: border-box; }
  html, body {
    width: 1200px;
    height: 959px;
    overflow: hidden;
    background: var(--backdrop);
    font-family: "Open Sans", Arial, sans-serif;
    color: var(--ink);
  }
  .stage {
    position: relative;
    width: 1200px;
    height: 959px;
  }
  .card {
    position: absolute;
    top: 336px;
    width: 500px;
    height: 286px;
    border-radius: 2px;
  }
  .card--front {
    left: 80px;
    background: var(--card-white);
  }
  .card--back {
    left: 620px;
    background: var(--card-dark);
  }

  /* Front: brand */
  .brand {
    position: absolute;
    left: 44px;
    top: 90px;
    display: flex;
    align-items: center;
    gap: 14px;
  }
  .brand__dot {
    width: 40px;
    height: 40px;
    border-radius: 50%;
    background: var(--ink);
  }
  .brand__name {
    font-size: 22px;
    font-weight: 400;
    letter-spacing: 2px;
    line-height: 24px;
    color: var(--ink);
    text-transform: uppercase;
  }

  /* Front: address */
  .address {
    position: absolute;
    right: 210px;
    top: 168px;
    text-align: right;
    font-size: 10px;
    line-height: 14px;
    font-style: normal;
    color: var(--ink-soft);
  }

  /* Front: person + contact */
  .person {
    position: absolute;
    left: 312px;
    top: 66px;
  }
  .person__name {
    font-size: 12px;
    font-weight: 700;
    letter-spacing: 0.3px;
    color: var(--ink);
  }
  .person__role {
    font-size: 10px;
    color: var(--ink-soft);
    margin-bottom: 16px;
  }
  .contact {
    list-style: none;
    font-size: 10px;
    line-height: 14px;
    color: var(--ink-soft);
  }
  .contact__web strong { font-weight: 700; color: var(--ink); }

  /* Back */
  .back__frame {
    position: absolute;
    inset: 16px;
  }
  .back__pattern {
    position: absolute;
    inset: 18px;
    border-radius: 12px;
    background: radial-gradient(circle at 50% 50%, var(--pattern-light) 0%, var(--card-dark) 55%, var(--pattern-dark) 100%);
    opacity: 0.85;
  }
</style>
</head>
<body>
<main class="stage">
  <section class="card card--front" aria-label="Business card front">
    <div class="brand">
      <span class="brand__dot" aria-hidden="true"></span>
      <span class="brand__name">Corvane<br>Casino</span>
    </div>
    <address class="address">
      CORVANE LIMITED<br>
      12, Harbour View Road<br>
      Colombo 01000, Sri Lanka
    </address>
    <div class="person">
      <p class="person__name">DAVID FERNANDO</p>
      <p class="person__role">Manager</p>
      <ul class="contact">
        <li>Tel: + 94 11 2456780</li>
        <li>Fax: + 94 11 2456781</li>
        <li class="contact__web">www.<strong>corvanecolombo</strong>.com</li>
      </ul>
    </div>
  </section>

  <section class="card card--back" aria-label="Business card back">
    <div class="back__pattern" role="img" aria-label="Repeating pattern of card-suit clubs in silver on charcoal"></div>
    <svg class="back__frame" width="468" height="254" viewBox="0 0 468 254" aria-hidden="true">
      <rect x="0.75" y="0.75" width="466.5" height="252.5" rx="14" ry="14" fill="none" stroke="var(--frame-line)" stroke-width="1.5"/>
    </svg>
  </section>
</main>
</body>
</html>
```